Heron Loan Partners Business Card

We need a business card design for our mortgage servicing company. In addition to servicing the loans of homeowners, we help homeowners with purchasing their homes and any mortgage refinancing. We would like to see designs that use the colors in the logo attached below (gold-ish yellow and navy blue), and any other design you deem fit! The design should communicate a simpler life with smart mortgages provided by Heron.

```html
<!DOCTYPE html>
<html lang="en">
<head>
<meta charset="utf-8">
<title>Heron Loan Partners Business Card</title>
<link rel="stylesheet" href="https://fonts.googleapis.com/css2?family=Lato:wght@400;700&family=Montserrat:wght@400;700&display=swap">
<style>
  :root {
    --stage: #2a2c30;
    --navy: #262159;
    --navy-deep: #1d1946;
    --gold: #e3b43a;
    --white: #ffffff;
    --muted: #d9d8e6;
  }
  * { box-sizing: border-box; margin: 0; padding: 0; }
  html, body { width: 1200px; height: 952px; overflow: hidden; }
  body {
    background: var(--stage);
    display: flex;
    flex-direction: column;
    align-items: center;
    justify-content: center;
    gap: 64px;
    font-family: "Lato", sans-serif;
  }
  .card {
    position: relative;
    width: 630px;
    height: 360px;
    background: var(--navy);
    border-radius: 22px;
    overflow: hidden;
    box-shadow: 0 18px 40px rgba(0,0,0,.45);
  }
  .card__edge-shade {
    position: absolute;
    left: 0; top: 0;
    width: 38px; height: 100%;
    background: var(--navy-deep);
    clip-path: polygon(0 0, 100% 0, 100% 62%, 0 72%);
  }
  .card__edge-gold {
    position: absolute;
    left: 0; bottom: 0;
    width: 38px; height: 48%;
    background: var(--gold);
    clip-path: polygon(0 22%, 100% 0, 100% 100%, 0 100%);
  }
  .brand {
    display: flex;
    align-items: center;
    gap: 12px;
    font-family: "Montserrat", sans-serif;
    font-weight: 700;
    color: var(--gold);
    letter-spacing: .02em;
  }
  .brand__dot {
    width: 14px; height: 14px;
    border-radius: 50%;
    background: var(--gold);
    flex: none;
  }
  /* front */
  .card--front .brand {
    position: absolute;
    left: 50%; top: 50%;
    transform: translate(-50%, -50%);
    font-size: 38px;
    white-space: nowrap;
  }
  /* back */
  .card--back .brand {
    position: absolute;
    left: 78px; top: 70px;
    font-size: 26px;
    white-space: nowrap;
  }
  .contact {
    position: absolute;
    right: 48px; top: 150px;
    width: 300px;
  }
  .contact__name {
    font-family: "Montserrat", sans-serif;
    font-size: 21px;
    color: var(--gold);
    text-transform: uppercase;
    letter-spacing: .03em;
    font-weight: 400;
  }
  .contact__name strong { font-weight: 700; }
  .contact__title {
    color: var(--white);
    font-size: 15px;
    margin-top: 2px;
  }
  .contact__rule {
    width: 52px; height: 2px;
    background: var(--gold);
    margin: 10px 0 12px;
  }
  .contact__list { list-style: none; }
  .contact__item {
    display: flex;
    align-items: flex-start;
    gap: 10px;
    color: var(--white);
    font-size: 13.5px;
    line-height: 1.35;
    margin-bottom: 7px;
  }
  .icon {
    width: 18px; height: 18px;
    border-radius: 3px;
    background: var(--gold);
    flex: none;
    margin-top: 1px;
  }
  .icon--pin { background: var(--white); }
  .icon svg { display: block; width: 18px; height: 18px; }
</style>
</head>
<body>

<section class="card card--front" aria-label="Business card front">
  <div class="card__edge-shade"></div>
  <div class="card__edge-gold"></div>
  <div class="brand"><span class="brand__dot"></span>Heron Loan Partners</div>
</section>

<section class="card card--back" aria-label="Business card back">
  <div class="card__edge-shade"></div>
  <div class="card__edge-gold"></div>
  <div class="brand"><span class="brand__dot"></span>Heron Loan Partners</div>

  <div class="contact">
    <p class="contact__name">Daniel R. <strong>Whitford</strong></p>
    <p class="contact__title">Managing Director</p>
    <div class="contact__rule"></div>
    <ul class="contact__list">
      <li class="contact__item">
        <span class="icon icon--pin"><svg viewBox="0 0 18 18"><path d="M9 3.5a3.6 3.6 0 0 0-3.6 3.6c0 2.7 3.6 7 3.6 7s3.6-4.3 3.6-7A3.6 3.6 0 0 0 9 3.5z" fill="#262159"/><circle cx="9" cy="7.1" r="1.3" fill="#fff"/></svg></span>
        <span>2710 Lakeside Avenue<br>Arlington, VA 22201</span>
      </li>
      <li class="contact__item">
        <span class="icon"><svg viewBox="0 0 18 18"><path d="M6 4l2 2.3-1.2 1.4a7 7 0 0 0 3.5 3.5l1.4-1.2L14 12l-1.2 1.6C9 13.6 4.4 9 4.4 5.2z" fill="#262159"/></svg></span>
        <span>+00 987 654 32</span>
      </li>
      <li class="contact__item">
        <span class="icon"><svg viewBox="0 0 18 18"><rect x="3.5" y="5" width="11" height="8" fill="none" stroke="#262159" stroke-width="1.4"/><path d="M3.5 5l5.5 4.5L14.5 5" fill="none" stroke="#262159" stroke-width="1.4"/></svg></span>
        <span>hello@heronloan.com</span>
      </li>
      <li class="contact__item">
        <span class="icon"><svg viewBox="0 0 18 18"><path d="M6 4l7 5.5-3 .6 1.8 3.4-1.3.7-1.8-3.4L6 13z" fill="#262159"/></svg></span>
        <span>www.heronloan.com</span>
      </li>
    </ul>
  </div>
</section>

</body>
</html>
```